Real Estate investment company needs billboard designs

This is our website: https://brightlanepropertygroup.com/
We are looking for some billboard concepts that uses our CEO in the design. I have attached some images and 1 billboard design that someone in our industry uses, but we don't want it exactly like his.

Industry/Entity Type

real estate

Colors

Designer to choose colors to be used in the design.

Requirements
Must have
• Company colors from websiute

```html
<!DOCTYPE html>
<html lang="en">
<head>
<meta charset="UTF-8">
<title>Bright Lane Property Group — Billboard</title>
<link href="https://fonts.googleapis.com/css2?family=Montserrat:wght@600;700;800;900&display=swap" rel="stylesheet">
<style>
  :root {
    --brand-red: #fb1010;
    --ink: #0d0d0d;
    --band-dark: #231f20;
    --paper: #ffffff;
    --backdrop: #6e6e6e;
    --photo-top: #c9d3de;
    --photo-bottom: #8fa6c2;
  }
  * { margin: 0; padding: 0; box-sizing: border-box; }
  html, body {
    width: 1071px; height: 1200px; overflow: hidden;
    background: var(--backdrop);
    font-family: "Montserrat", Arial, sans-serif;
  }
  .billboard {
    position: absolute; left: 28px; top: 366px;
    width: 1015px; height: 469px;
    background: var(--paper);
    overflow: hidden;
    box-shadow: 0 4px 10px rgba(0,0,0,0.35);
  }
  .roof-chevron {
    position: absolute; left: 0; top: 0;
    width: 1015px; height: 469px;
  }
  .brand-name {
    position: absolute; left: 21px; top: 42px;
    display: inline-flex; flex-direction: column;
    color: var(--ink); font-weight: 800; line-height: 1;
  }
  .brand-name .line-main { font-size: 84px; letter-spacing: -1.5px; }
  .brand-name .line-sub { font-size: 40px; margin-top: 14px; align-self: flex-end; letter-spacing: 0.5px; }
  .offer-line {
    position: absolute; left: 21px; top: 268px;
    font-size: 40px; font-weight: 800; color: var(--ink);
    letter-spacing: -0.6px; line-height: 1;
  }
  .headline {
    position: absolute; left: 19px; top: 318px;
    font-size: 64px; font-weight: 900; color: var(--brand-red);
    letter-spacing: -1px; line-height: 1;
  }
  .ceo-photo {
    position: absolute; left: 712px; top: 62px;
    width: 303px; height: 350px;
    border-radius: 120px 0 0 0;
    background: linear-gradient(180deg, var(--photo-top), var(--photo-bottom));
  }
  .contact-band {
    position: absolute; left: 0; bottom: 0; width: 100%; height: 57px;
    background: var(--band-dark);
  }
  .contact-band .phone-panel {
    position: absolute; left: 0; top: 0; height: 100%; width: 518px;
    background: var(--brand-red);
    clip-path: polygon(0 0, 100% 0, 94.5% 100%, 0 100%);
    display: flex; align-items: center; padding-left: 18px; gap: 10px;
  }
  .contact-band .phone-number {
    color: var(--paper); font-size: 54px; font-weight: 800;
    letter-spacing: -1.5px; line-height: 1;
  }
  .contact-band .divider-stripe {
    position: absolute; left: 500px; top: 0; width: 14px; height: 100%;
    background: var(--paper);
    clip-path: polygon(60% 0, 100% 0, 40% 100%, 0 100%);
  }
  .contact-band .web-panel {
    position: absolute; left: 525px; top: 0; height: 100%; right: 18px;
    display: flex; align-items: center; justify-content: flex-end; gap: 8px;
  }
  .contact-band .web-address {
    color: var(--paper); font-size: 27px; font-weight: 700; letter-spacing: -0.3px;
  }
  .contact-band .web-address .tld { color: var(--brand-red); }
</style>
</head>
<body>
  <main class="billboard">
    <svg class="roof-chevron" viewBox="0 0 1015 469" aria-hidden="true">
      <polygon fill="#fb1010" points="932,1 1015,58 1015,136 932,79 734,216 707,156"/>
    </svg>

    <div class="brand-name">
      <span class="line-main">BRIGHT LANE</span>
      <span class="line-sub">PROPERTY GROUP</span>
    </div>

    <p class="offer-line">Get a Cash Offer, Same Day.</p>
    <p class="headline">Selling Your Home?</p>

    <div class="ceo-photo" role="img" aria-label="Photo of the company CEO smiling and pointing upward, wearing a light blue denim shirt"></div>

    <footer class="contact-band">
      <div class="phone-panel">
        <svg class="phone-icon" width="40" height="40" viewBox="0 0 24 24" aria-hidden="true">
          <path fill="#ffffff" d="M6.6 10.8a15.1 15.1 0 0 0 6.6 6.6l2.2-2.2a1 1 0 0 1 1-.25 11.4 11.4 0 0 0 3.6.57 1 1 0 0 1 1 1V20a1 1 0 0 1-1 1A17 17 0 0 1 3 4a1 1 0 0 1 1-1h3.5a1 1 0 0 1 1 1c0 1.25.2 2.45.57 3.6a1 1 0 0 1-.25 1z"/>
          <path fill="none" stroke="#ffffff" stroke-width="1.8" stroke-linecap="round" d="M14.5 2.5a7 7 0 0 1 7 7M14.5 6a3.5 3.5 0 0 1 3.5 3.5"/>
        </svg>
        <span class="phone-number">865-555-0142</span>
      </div>
      <div class="divider-stripe"></div>
      <div class="web-panel">
        <svg class="globe-icon" width="34" height="34" viewBox="0 0 24 24" aria-hidden="true">
          <g fill="none" stroke="#fb1010" stroke-width="1.6">
            <circle cx="12" cy="12" r="10"/>
            <ellipse cx="12" cy="12" rx="4.5" ry="10"/>
            <path d="M2 12h20M3.5 7h17M3.5 17h17M12 2v20"/>
          </g>
        </svg>
        <span class="web-address">brightlanepropertygroup<span class="tld">.com</span></span>
      </div>
    </footer>
  </main>
</body>
</html>
```